Web Design For Manufacturing And Outsourcing Company

Pick up the pieces from our previous developer and help us complete our website.

5 pages - Home,Machining,Sourcing,About Us, and Contact

Attached you will find screen shots of previous direction but we're open to new ideas.

We can provide all text and images needed.

Thanks!

Number of Pages Required

5+ page

```html
<!DOCTYPE html>
<html lang="en">
<head>
<meta charset="utf-8">
<title>Corvan Industries</title>
<link href="https://fonts.googleapis.com/css2?family=Montserrat:wght@400;600;700&family=Arimo:wght@400;700&display=swap" rel="stylesheet">
<style>
:root{
  --orange:#ee5323;
  --orange-deep:#d9431a;
  --ink:#333333;
  --text:#555555;
  --muted:#777777;
  --light:#f4f4f4;
  --dark:#1f1f1f;
  --white:#ffffff;
  --line:#e2e2e2;
}
*{margin:0;padding:0;box-sizing:border-box}
html,body{width:1200px;height:3358px;overflow:hidden}
body{position:relative;background:var(--white);font-family:"Arimo",Arial,sans-serif;color:var(--text)}
.abs{position:absolute}
.heading{font-family:"Montserrat",sans-serif;font-weight:700;color:var(--ink)}
.btn{position:absolute;display:flex;align-items:center;justify-content:center;border-radius:30px;background:var(--orange);color:var(--white);font-family:"Montserrat",sans-serif;font-weight:700;font-size:14px;box-shadow:0 3px 6px rgba(0,0,0,.25)}

/* top + nav */
.top-strip{left:0;top:0;width:1200px;height:63px;background:linear-gradient(90deg,#222,#3a3530,#222)}
.nav-bar{left:0;top:63px;width:1200px;height:105px;background:var(--white)}
.brand{left:120px;top:90px;display:flex;align-items:center;gap:10px;font-family:"Montserrat",sans-serif;font-weight:700;font-size:15px;letter-spacing:2px;color:var(--orange)}
.brand-mark{width:30px;height:30px;background:var(--orange)}
.nav{left:560px;top:101px;display:flex;align-items:center;font-family:"Montserrat",sans-serif;font-weight:600;font-size:12px;color:#222}
.nav a{color:inherit;text-decoration:none}
.nav .home{width:76px;height:36px;border-radius:18px;background:var(--orange);color:var(--white);display:flex;align-items:center;justify-content:center}
.nav .m{margin-left:38px}
.nav .s{margin-left:55px}
.nav .c{margin-left:55px}

/* hero */
.hero-photo{left:0;top:168px;width:1200px;height:682px;background:radial-gradient(ellipse at 60% 40%,#5a4738 0%,#2d2620 55%,#151210 100%)}
.hero-title{left:0;top:350px;width:1200px;text-align:center;font-family:"Montserrat",sans-serif;font-weight:700;font-size:64px;color:var(--white);letter-spacing:1px}
.hero-title span{color:var(--orange)}
.hero-text{left:250px;top:448px;width:700px;text-align:center;font-size:17px;line-height:30px;color:var(--white)}
.hero-btn{left:522px;top:537px;width:156px;height:52px}
.hero-edge{left:0;top:690px}

/* about */
.about-title{left:114px;top:948px;font-size:44px}
.about-title span{color:var(--orange)}
.about-text{left:114px;top:1012px;width:314px;font-size:12.5px;line-height:25.5px;text-align:justify;color:#333}
.about-btn{left:112px;top:1247px;width:136px;height:52px}
.frame-top{left:486px;top:909px;width:407px;height:8px;background:var(--orange)}
.frame-side{left:486px;top:909px;width:8px;height:385px;background:var(--orange)}
.about-photo{left:515px;top:938px;width:573px;height:385px;background:linear-gradient(135deg,#1d2a3a 0%,#3c4e62 45%,#8a98a6 75%,#2a3340 100%)}

/* sourcing */
.sourcing{left:0;top:1388px;width:1200px;height:676px;background:var(--light)}
.sec-title{left:0;width:1200px;text-align:center;font-size:44px}
.sec-sub{left:0;width:1200px;text-align:center;font-size:12px;color:#444}
.sourcing-photo{left:132px;top:1540px;width:363px;height:464px;background:radial-gradient(circle at 50% 42%,#7fa6c4 0%,#24435e 35%,#0d1a28 80%)}
.s-item{left:540px;width:560px;height:110px}
.s-icon{position:absolute;left:0;top:0;width:76px;height:76px;border-radius:50%;border:2px solid #dcdcdc;background:var(--white);display:flex;align-items:center;justify-content:center}
.s-name{position:absolute;left:100px;top:0;font-family:"Montserrat",sans-serif;font-weight:600;font-size:15px;color:#222}
.s-text{position:absolute;left:100px;top:30px;width:440px;font-size:12px;line-height:25px;color:var(--muted)}

/* machining */
.m-card{width:273px;background:var(--white);border:1px solid var(--line);text-align:center}
.m-card svg{display:block;margin:20px auto 0}
.m-name{margin-top:12px;font-family:"Montserrat",sans-serif;font-weight:600;font-size:12.5px;color:#222}
.m-text{margin:10px auto 0;width:220px;font-size:12px;line-height:25px;color:var(--muted)}
.machine-photo{left:699px;top:2223px;width:362px;height:461px;background:linear-gradient(160deg,#2b2b2b 0%,#777 40%,#c9c9c9 70%,#4a4a4a 100%)}

/* cta */
.cta{left:0;top:2745px;width:1200px;height:351px;background:linear-gradient(120deg,#f27a45 0%,#e8612c 45%,#c9471d 100%)}
.cta-1{left:0;top:2830px;width:1200px;text-align:center;font-family:"Montserrat",sans-serif;font-weight:700;font-size:40px;color:var(--white)}
.cta-2{left:0;top:2892px;width:1200px;text-align:center;font-family:"Montserrat",sans-serif;font-weight:600;font-size:35px;color:var(--white)}
.cta-btn{left:493px;top:2962px;width:215px;height:56px;border:2px solid var(--white);border-radius:30px;display:flex;align-items:center;justify-content:center;font-family:"Montserrat",sans-serif;font-weight:700;font-size:17px;color:var(--white)}

/* footer */
.footer{left:0;top:3096px;width:1200px;height:262px;background:var(--dark)}
.foot-brand{left:0;top:3190px;width:1200px;display:flex;justify-content:center;align-items:center;gap:10px;font-family:"Montserrat",sans-serif;font-weight:700;font-size:15px;letter-spacing:2px;color:var(--orange)}
.foot-contact{left:0;top:3256px;width:1200px;display:flex;justify-content:center;align-items:center;font-size:13px;color:#ddd}
.foot-contact .item{display:flex;align-items:center;gap:8px}
.foot-contact .sep{margin:0 30px;color:#bbb}
.copy{left:0;top:3304px;width:1200px;text-align:center;font-size:12px;color:#ddd}
</style>
</head>
<body>

<div class="abs top-strip"></div>
<header class="abs nav-bar"></header>
<div class="abs brand"><span class="brand-mark"></span>CORVAN INDUSTRIES</div>
<nav class="abs nav">
  <a class="home">HOME</a>
  <a class="m">MACHINING CAPABILITIES</a>
  <a class="s">SOURCING</a>
  <a class="c">CONTACT US</a>
</nav>

<div class="abs hero-photo" role="img" aria-label="Close-up of a machining tool cutting metal with sparks"></div>
<h1 class="abs hero-title"><span>CORVAN</span> INDUSTRIES</h1>
<p class="abs hero-text">Corvan Industries brings their machining knowledge to the table every day working closely with our customers to put value into each part we produce.</p>
<div class="btn hero-btn">READ MORE</div>
<svg class="abs hero-edge" width="1200" height="170" viewBox="0 0 1200 170">
  <polygon points="0,18 360,162 1200,18 1200,170 0,170" fill="#ffffff"/>
  <polyline points="0,14 360,160 1200,14" fill="none" stroke="#ee5323" stroke-width="5"/>
  <polygon points="0,6 360,152 0,22" fill="#ee5323"/>
</svg>

<h2 class="abs heading about-title">ABOUT <span>US</span></h2>
<p class="abs about-text">We are committed to consistently exceeding customer expectations by providing products, services and sourcing solutions of the highest standard of quality. With our streamlined processes our method is efficient, provides value and ensures on time delivery. Our success is based on continuously improving the efficiencies and effectiveness of our products, processes, and quality management systems. We are one company, one team.</p>
<div class="btn about-btn">READ MORE</div>
<div class="abs frame-top"></div>
<div class="abs frame-side"></div>
<div class="abs about-photo" role="img" aria-label="Machinist in a hard hat operating a CNC control panel"></div>

<section class="abs sourcing"></section>
<h2 class="abs heading sec-title" style="top:1420px">SOURCING</h2>
<p class="abs sec-sub" style="top:1493px">Over the years we identified the need to provide one stop services to purchasing departments.</p>
<div class="abs sourcing-photo" role="img" aria-label="Hand holding a glowing light bulb surrounded by energy icons"></div>

<div class="abs s-item" style="top:1556px">
  <div class="s-icon"><svg width="40" height="40" viewBox="0 0 40 40" fill="none" stroke="#ee5323" stroke-width="2"><rect x="8" y="8" width="24" height="24" rx="3"/><path d="M14 20l5 5 8-10"/></svg></div>
  <div class="s-name">VETTING</div>
  <p class="s-text">Over the years we identified the need to provide one stop services to purchas of hard to find products, economical alternatives to our customers.</p>
</div>
<div class="abs s-item" style="top:1675px">
  <div class="s-icon"><svg width="40" height="40" viewBox="0 0 40 40" fill="none" stroke="#ee5323" stroke-width="2"><circle cx="20" cy="20" r="13"/><circle cx="20" cy="20" r="7"/><path d="M20 3v4M20 33v4M3 20h4M33 20h4"/></svg></div>
  <div class="s-name">QUALITY</div>
  <p class="s-text">Over the years we identified the need to provide one stop services to purchas of hard to find products, economical alternatives to our customers.</p>
</div>
<div class="abs s-item" style="top:1793px">
  <div class="s-icon"><svg width="40" height="40" viewBox="0 0 40 40" fill="none" stroke="#ee5323" stroke-width="2"><circle cx="10" cy="12" r="4"/><circle cx="30" cy="28" r="4"/><path d="M14 12h16v8H10v8h16"/></svg></div>
  <div class="s-name">PROCESS</div>
  <p class="s-text">Over the years we identified the need to provide one stop services to purchas of hard to find products, economical alternatives to our customers.</p>
</div>
<div class="abs s-item" style="top:1912px">
  <div class="s-icon"><svg width="40" height="40" viewBox="0 0 40 40" fill="none" stroke="#ee5323" stroke-width="2"><path d="M6 34h28"/><rect x="8" y="24" width="5" height="10"/><rect x="16" y="19" width="5" height="15"/><rect x="24" y="13" width="5" height="21"/><path d="M8 16l10-7 6 3 9-6"/></svg></div>
  <div class="s-name">BENEFITS</div>
  <p class="s-text">Over the years we identified the need to provide one stop services to purchas of hard to find products, economical alternatives to our customers.</p>
</div>

<h2 class="abs heading sec-title" style="top:2100px">MACHINING</h2>
<p class="abs sec-sub" style="top:2174px">Corvan Industries brings their machining knowledge to the table every day working closely with our customers to put value into each part we produce.</p>

<div class="abs m-card" style="left:112px;top:2223px;height:217px">
  <svg width="70" height="70" viewBox="0 0 70 70" fill="none" stroke="#ee5323" stroke-width="2.5"><circle cx="35" cy="14" r="6"/><path d="M35 20v12M20 34h30M20 34l-8 14M50 34l8 14M12 48l-4 10M12 48l6 8M58 48l4 10M58 48l-6 8"/><circle cx="35" cy="36" r="5"/></svg>
  <div class="m-name">MULTIPLE AXIS EQUIPMENT</div>
  <p class="m-text">Corvan Industries brings their machining knowledge to the table every day working</p>
</div>
<div class="abs m-card" style="left:401px;top:2223px;height:217px">
  <svg width="70" height="70" viewBox="0 0 70 70" fill="none" stroke="#ee5323" stroke-width="2.5"><path d="M14 14l42 42M10 18l8-8 8 8-8 8zM56 14L14 56M50 8a8 8 0 1 0 12 12l-6-2-4-4z"/></svg>
  <div class="m-name">CUSTOM BUILT FIXTURES/TOOLING</div>
  <p class="m-text">Corvan Industries brings their machining knowledge to the table every day working</p>
</div>
<div class="abs m-card" style="left:112px;top:2470px;height:214px">
  <svg width="70" height="70" viewBox="0 0 70 70" fill="none" stroke="#ee5323" stroke-width="2.5"><rect x="10" y="30" width="18" height="24"/><rect x="42" y="30" width="18" height="24"/><circle cx="19" cy="20" r="6"/><circle cx="51" cy="20" r="6"/><path d="M6 58h58M28 42h14"/></svg>
  <div class="m-name">ASSEMBLIES</div>
  <p class="m-text">Corvan Industries brings their machining knowledge to the table every day working</p>
</div>
<div class="abs m-card" style="left:401px;top:2470px;height:214px">
  <svg width="70" height="70" viewBox="0 0 70 70" fill="none" stroke="#ee5323" stroke-width="2.5"><rect x="10" y="14" width="50" height="36"/><path d="M10 24h50M18 32h14M18 40h20M44 32h8v10h-8zM20 58h30"/></svg>
  <div class="m-name">PROTOTYPES TO PRODUCTION RUNS</div>
  <p class="m-text">Corvan Industries brings their machining knowledge to the table every day working</p>
</div>
<div class="abs machine-photo" role="img" aria-label="Precision machine head working on a metal part"></div>

<section class="abs cta" role="img" aria-label="Orange-toned view of machining equipment"></section>
<div class="abs cta-1">CONTACT US TODAY</div>
<div class="abs cta-2">WITH YOUR MACHINING OR SOURCING NEEDS!</div>
<div class="abs cta-btn">GET IN TOUCH</div>

<footer class="abs footer"></footer>
<div class="abs foot-brand"><span class="brand-mark"></span>CORVAN INDUSTRIES</div>
<div class="abs foot-contact">
  <span class="item"><svg width="13" height="13" viewBox="0 0 24 24" fill="#fff"><path d="M6.6 10.8a15 15 0 0 0 6.6 6.6l2.2-2.2a1 1 0 0 1 1-.25 11 11 0 0 0 3.6.6 1 1 0 0 1 1 1V20a1 1 0 0 1-1 1A17 17 0 0 1 3 4a1 1 0 0 1 1-1h3.5a1 1 0 0 1 1 1 11 11 0 0 0 .6 3.6 1 1 0 0 1-.25 1z"/></svg>Phone: 555 204-1180</span>
  <span class="sep">|</span>
  <span class="item"><svg width="14" height="11" viewBox="0 0 24 18" fill="#fff"><path d="M0 0h24v18H0zM2 2v1l10 7 10-7V2z" fill-rule="evenodd"/></svg>Email: info@corvan-ind.com</span>
  <span class="sep">|</span>
  <span class="item"><svg width="11" height="15" viewBox="0 0 16 22" fill="#fff"><path d="M8 0a8 8 0 0 0-8 8c0 6 8 14 8 14s8-8 8-14a8 8 0 0 0-8-8zm0 11a3 3 0 1 1 0-6 3 3 0 0 1 0 6z"/></svg>1200 Meadow Rd. Lakeview MI. 48000</span>
</div>
<div class="abs copy">© Copyright -2019 Corvan Industries All rights reserved.</div>

</body>
</html>
```